Executive Business Card for Healthcare Company [Need Today]

I need a business card design for a healthcare company. The only branding the company has thus far is a logo. The cards will be utilized by company executives. The design I envision will be vibrant and appealing but with a corporate feel. They shouldn't be too casual or playful. I would like to complete this project TODAY if possible.

Target Market(s)

Healthcare vendors, other executives in healthcare and pharmaceuticals

Industry/Entity Type

Pharmaceutical

Contact Information for Business Card

See attachment

Font styles to use
Serif
Sans Serif

Colors

Designer to choose colors to be used in the design.

```html
<!DOCTYPE html>
<html lang="en">
<head>
<meta charset="utf-8">
<title>Corvane Therapeutics – Business Card</title>
<link href="https://fonts.googleapis.com/css2?family=Raleway:wght@300;400&family=Roboto:wght@300;400&display=swap" rel="stylesheet">
<style>
  :root {
    --bg: #e6e7e9;
    --card: #ffffff;
    --card-back: #f4f5f5;
    --teal: #1fa7b8;
    --green: #4dbb8a;
    --grey-text: #6f7375;
    --dark-text: #4a4d4f;
    --rule: #b9bcbe;
    --faint: #e6e8e8;
  }
  * { box-sizing: border-box; margin: 0; padding: 0; }
  html, body { width: 1200px; height: 726px; overflow: hidden; background: var(--bg); }
  body { position: relative; font-family: "Roboto", Arial, sans-serif; }

  .card {
    position: absolute;
    top: 213px;
    width: 525px;
    height: 300px;
    overflow: hidden;
    box-shadow: 0 6px 18px rgba(0,0,0,0.12);
  }
  .card--front { left: 50px; background: var(--card); }
  .card--back { left: 625px; background: var(--card-back); }

  /* Front */
  .front-lockup {
    position: absolute;
    top: 86px; left: 0; right: 0;
    display: flex; align-items: center; justify-content: center; gap: 18px;
  }
  .brand-dot {
    width: 80px; height: 80px; border-radius: 50%;
    border: 3px solid var(--green);
  }
  .lockup-rule { width: 1px; height: 56px; background: var(--rule); }
  .brand-name {
    font-family: "Raleway", Arial, sans-serif;
    font-weight: 300;
    color: var(--teal);
    line-height: 1.05;
  }
  .front-lockup .brand-name { font-size: 38px; }
  .brand-name span { display: block; }
  .front-web {
    position: absolute; bottom: 46px; left: 0; right: 0;
    text-align: center;
    font-size: 14px; letter-spacing: 4px;
    color: var(--dark-text);
  }
  .front-web em { font-style: normal; color: var(--teal); }

  /* Back */
  .back-deco {
    position: absolute; right: -60px; top: -40px;
    width: 260px; height: 260px; border-radius: 50%;
    border: 14px solid var(--faint);
  }
  .back-brand {
    position: absolute; left: 40px; top: 70px;
    display: flex; flex-direction: column; align-items: flex-start; gap: 14px;
  }
  .back-brand .brand-dot { width: 66px; height: 66px; margin-left: 30px; }
  .back-brand .brand-name { font-size: 30px; }

  .contact { position: absolute; left: 290px; top: 52px; color: var(--dark-text); }
  .contact-name { font-size: 22px; font-weight: 400; color: var(--teal); }
  .contact-title { font-size: 10px; color: var(--grey-text); margin: 3px 0 12px; }
  .contact-list { list-style: none; font-size: 12.5px; font-weight: 300; line-height: 1.55; }
  .contact-list li { display: flex; align-items: center; gap: 7px; }
  .contact-list svg { width: 11px; height: 11px; fill: var(--dark-text); flex: none; }
  .contact-list .indent { padding-left: 18px; }
  .contact-list em { font-style: normal; color: var(--teal); }

  .web-band {
    position: absolute; right: 0; bottom: 0;
    width: 250px; height: 52px;
    background: linear-gradient(90deg, var(--teal), var(--green));
    clip-path: polygon(14px 0, 100% 0, 100% 100%, 0 100%);
    display: flex; align-items: center; justify-content: center;
    color: #fff; font-size: 13px; letter-spacing: 0.5px;
  }
</style>
</head>
<body>

  <section class="card card--front" aria-label="Card front">
    <div class="front-lockup">
      <div class="brand-dot"></div>
      <div class="lockup-rule"></div>
      <div class="brand-name"><span>corvane</span><span>therapeutics</span></div>
    </div>
    <p class="front-web">www.<em>corvanerx</em>.com</p>
  </section>

  <section class="card card--back" aria-label="Card back">
    <div class="back-deco"></div>
    <div class="back-brand">
      <div class="brand-dot"></div>
      <div class="brand-name"><span>corvane</span><span>therapeutics</span></div>
    </div>
    <div class="contact">
      <p class="contact-name">Daniel Hartwell</p>
      <p class="contact-title">Senior Director of Marketing</p>
      <ul class="contact-list">
        <li><svg viewBox="0 0 24 24"><path d="M6.6 10.8a15 15 0 0 0 6.6 6.6l2.2-2.2a1 1 0 0 1 1-.25 11.4 11.4 0 0 0 3.6.57 1 1 0 0 1 1 1V20a1 1 0 0 1-1 1A17 17 0 0 1 3 4a1 1 0 0 1 1-1h3.5a1 1 0 0 1 1 1c0 1.25.2 2.45.57 3.57a1 1 0 0 1-.25 1z"/></svg>555-210-4837</li>
        <li><svg viewBox="0 0 24 24"><path d="M7 1h10a2 2 0 0 1 2 2v18a2 2 0 0 1-2 2H7a2 2 0 0 1-2-2V3a2 2 0 0 1 2-2zm0 3v14h10V4zm5 15.5a1 1 0 1 0 0 2 1 1 0 0 0 0-2z"/></svg>555-370-6142</li>
        <li><svg viewBox="0 0 24 24"><path d="M2 5h20v14H2zm2 2v.5l8 5 8-5V7zm0 2.8V17h16V9.8l-8 5z"/></svg>dhartwell@<em>corvanerx</em>.com</li>
        <li><svg viewBox="0 0 24 24"><path d="M12 2a7 7 0 0 0-7 7c0 5.25 7 13 7 13s7-7.75 7-13a7 7 0 0 0-7-7zm0 9.5a2.5 2.5 0 1 1 0-5 2.5 2.5 0 0 1 0 5z"/></svg>118 W Linden Avenue</li>
        <li class="indent">Fairview, OH 44120</li>
      </ul>
    </div>
    <div class="web-band">www.corvanerx.com</div>
  </section>

</body>
</html>
```